Website design with eCommerce for revolutionary new product in the manufacturing industry.

We need a website designed for a precision manufacturing company based in the suburbs of Minneapolis, Minnesota called Velkrin Manufacturing. We have a revolutionary new product, the TARN LOCK, to introduce and sell through an eCommerce storefront. The website would include company information, product information, and the storefront. Green is a color that represents Velkrin Manufacturing. The final design should communicate that we exclusively offer premium products at a premium price. The design should also let the customer know they are the focus of our work.

Target Market(s)

Machinists and machine shops

Industry/Entity Type

Manufacturing and machine shops

Coding

Coded - Design and coding required

Font styles to use
Sans Serif

Colors
59FF00
82FF00
B8FF75
E3FFCB
F4FFEA

Requirements
Must have
• eCommerce storefront, Made in USA references
Nice to have
• Home page, TARN LOCK Product page, About Us, Capabilities, Contact, etc.
Should not have
• Should not be too much text and reading.

```html
<!DOCTYPE html>
<html lang="en">
<head>
<meta charset="utf-8">
<title>Contact – TARN LOCK</title>
<link href="https://fonts.googleapis.com/css2?family=Orbitron:wght@700;900&family=Poppins:wght@400;500;600;700&display=swap" rel="stylesheet">
<style>
:root{
  --green:#59ff00;
  --bg:#151515;
  --bg-deep:#0c0c0c;
  --nav:#1a1a1a;
  --field:#2a2a2a;
  --text:#ffffff;
  --muted:#cfcfcf;
}
*{box-sizing:border-box;margin:0;padding:0}
html,body{width:672px;height:1200px;overflow:hidden;background:var(--bg);color:var(--text);font-family:"Poppins",sans-serif}
.page{position:relative;width:672px;height:1200px}
.abs{position:absolute}
.nav{left:0;top:0;width:672px;height:43px;background:var(--nav);z-index:2}
.brand{font-family:"Orbitron",sans-serif;font-weight:900;color:var(--text);letter-spacing:.5px}
.nav .brand{left:50px;top:13px;font-size:14px}
.nav-links{left:178px;top:17px;display:flex;gap:11px;font-size:6.6px;font-weight:600;letter-spacing:.1px}
.nav-cta{left:616px;top:0;width:56px;height:43px;background:var(--green);color:#111;font-size:7px;font-weight:700;display:flex;align-items:center;justify-content:center}
.hero{left:0;top:43px}
.hero-title{left:0;top:108px;width:672px;text-align:center;font-family:"Orbitron",sans-serif;font-weight:900;font-size:36px;letter-spacing:1px}
.section-title{left:0;top:276px;width:672px;text-align:center;font-family:"Orbitron",sans-serif;font-weight:700;font-size:20px;letter-spacing:1px}
.title-rule{left:313px;top:306px;width:34px;height:2px;background:var(--green)}
.intro{left:0;top:320px;width:672px;text-align:center;font-size:8px;color:var(--muted)}
.info{left:111px;display:flex;align-items:center;gap:9px}
.info-icon{width:37px;height:37px;border-radius:4px;background:var(--green);display:flex;align-items:center;justify-content:center}
.info-label{font-size:11px;color:var(--muted);line-height:1.2}
.info-value{font-size:13px;font-weight:700;color:#e6e6e6;line-height:1.2}
.label{font-size:6px;font-weight:700}
.field{background:var(--field);border-radius:2px;font-size:6.8px;color:#d8d8d8;padding:0 8px;display:flex;align-items:center}
.submit{left:339px;top:537px;width:225px;height:27px;background:var(--green);color:#111;font-weight:700;font-size:9px;display:flex;align-items:center;justify-content:center;border-radius:2px}
.submit svg{position:absolute;right:12px;top:8px}
.map-frame{left:105px;top:619px;width:464px;height:212px;background:#2a2a2a;border-radius:4px}
.map{left:110px;top:624px;width:454px;height:202px;background:linear-gradient(135deg,#e2e2e2,#cfcfcf);border-radius:3px}
.footer-bg{left:0;top:848px}
.footer-brand{left:0;top:950px;width:672px;text-align:center;font-size:19px}
.col-title{top:1008px;font-family:"Orbitron",sans-serif;font-weight:700;font-size:9px;letter-spacing:.3px}
.links{left:81px;top:1030px;font-size:6.6px;line-height:12.5px}
.social{left:214px;top:1034px;font-size:7px}
.social li{list-style:none;display:flex;align-items:center;gap:6px;height:20px}
.social span{width:13px;height:13px;background:#2a2a2a;border-radius:2px;display:inline-block}
.contact-col{left:330px;top:1034px;font-size:7px;line-height:11px;display:flex;gap:5px}
.mini-field{left:451px;width:145px;height:19px;font-size:6.6px}
.mini-submit{left:451px;top:1108px;width:51px;height:19px;background:#fff;color:#111;font-size:7px;font-weight:700;display:flex;align-items:center;justify-content:center;border-radius:2px}
.divider{left:49px;top:1169px;width:575px;height:1px;background:#333}
.copy{left:0;top:1183px;width:672px;text-align:center;font-size:7px;font-weight:600}
.to-top{left:635px;top:1158px;width:26px;height:26px;background:var(--green);display:flex;align-items:center;justify-content:center}
</style>
</head>
<body>
<div class="page">
  <header class="abs nav">
    <div class="abs brand">TARN LOCK</div>
    <nav class="abs nav-links">
      <span>WHY VELKRIN MANUFACTURING?</span><span>WHAT WE DO</span><span>HOW WE MAKE IT BETTER</span><span>CAPABILITIES</span><span>GALLERY</span><span>ABOUT US</span><span>WISDOM</span>
    </nav>
    <div class="abs nav-cta">CONTACT</div>
  </header>

  <svg class="abs hero" width="672" height="220" viewBox="0 43 672 220">
    <defs>
      <linearGradient id="metal" x1="0" y1="0" x2="1" y2="1">
        <stop offset="0" stop-color="#6b6a66"/><stop offset=".5" stop-color="#3d3b37"/><stop offset="1" stop-color="#5c574d"/>
      </linearGradient>
    </defs>
    <polygon role="img" aria-label="Close-up photo of machined metal parts" points="0,43 672,43 672,158 0,261" fill="url(#metal)"/>
    <polygon points="15,261 672,157 672,185 0,262" fill="var(--green)"/>
  </svg>
  <h1 class="abs hero-title">CONTACT</h1>

  <h2 class="abs section-title">GET IN TOUCH</h2>
  <div class="abs title-rule"></div>
  <p class="abs intro">Please fill out the information below to complete...</p>

  <div class="abs info" style="top:368px">
    <div class="info-icon"><svg width="16" height="16" viewBox="0 0 24 24"><path d="M6.6 10.8a15 15 0 0 0 6.6 6.6l2.2-2.2c.3-.3.7-.4 1-.2 1.1.4 2.3.6 3.6.6.6 0 1 .4 1 1V20c0 .6-.4 1-1 1A17 17 0 0 1 3 4c0-.6.4-1 1-1h3.5c.6 0 1 .4 1 1 0 1.3.2 2.5.6 3.6.1.3 0 .7-.2 1z" fill="#111"/></svg></div>
    <div><div class="info-label">Phone:</div><div class="info-value">123 4567 655</div></div>
  </div>
  <div class="abs info" style="top:420px">
    <div class="info-icon"><svg width="16" height="13" viewBox="0 0 24 18"><rect x="1" y="1" width="22" height="16" rx="2" fill="#111"/><path d="M2 3l10 7 10-7" stroke="#59ff00" stroke-width="2" fill="none"/></svg></div>
    <div><div class="info-label">Email:</div><div class="info-value">info@tarnlock.com</div></div>
  </div>
  <div class="abs info" style="top:472px">
    <div class="info-icon"><svg width="14" height="18" viewBox="0 0 14 20"><path d="M7 0a7 7 0 0 0-7 7c0 5 7 13 7 13s7-8 7-13a7 7 0 0 0-7-7z" fill="#111"/><circle cx="7" cy="7" r="2.6" fill="#59ff00"/></svg></div>
    <div><div class="info-label">Address:</div><div class="info-value">Some goes address here</div></div>
  </div>

  <div class="abs label" style="left:337px;top:367px">NAME*</div>
  <div class="abs label" style="left:453px;top:367px">EMAIL*</div>
  <div class="abs field" style="left:339px;top:378px;width:110px;height:23px">Enter your name</div>
  <div class="abs field" style="left:453px;top:378px;width:111px;height:23px">Enter your email</div>
  <div class="abs label" style="left:337px;top:406px">PHONE*</div>
  <div class="abs label" style="left:453px;top:406px">DATE*</div>
  <div class="abs field" style="left:339px;top:417px;width:110px;height:23px">Enter phone number</div>
  <div class="abs field" style="left:453px;top:417px;width:111px;height:23px;justify-content:space-between">Select date<svg width="6" height="4" viewBox="0 0 6 4"><path d="M.5.5 3 3 5.5.5" stroke="#59ff00" fill="none"/></svg></div>
  <div class="abs label" style="left:337px;top:448px">PHONE*</div>
  <div class="abs field" style="left:339px;top:458px;width:225px;height:63px;align-items:flex-start;padding-top:8px">Type your text...</div>
  <div class="abs submit">SUBMIT NOW<svg width="11" height="11" viewBox="0 0 24 24"><path d="M22 2 2 10l7 3 3 7z M22 2 9 13" stroke="#111" stroke-width="2.4" fill="none" stroke-linejoin="round"/></svg></div>

  <div class="abs map-frame"></div>
  <div class="abs map" role="img" aria-label="Street map showing the company location"></div>

  <svg class="abs footer-bg" width="672" height="352" viewBox="0 848 672 352">
    <polygon points="0,955 672,848 672,1200 0,1200" fill="var(--bg-deep)"/>
  </svg>
  <div class="abs brand footer-brand">TARN LOCK</div>

  <div class="abs col-title" style="left:80px">HELPFUL LINKS</div>
  <div class="abs col-title" style="left:216px">INFORMATION</div>
  <div class="abs col-title" style="left:330px">CONTACT US</div>
  <div class="abs col-title" style="left:449px">GET IN TOUCH</div>

  <div class="abs links">Why velkrin manufacturing?<br>What We Do<br>How We Make It Better<br>Capabilities<br>Gallery<br>About Us<br>Wisdom<br>Contact Us</div>
  <ul class="abs social">
    <li><span></span>Pagebook</li><li><span></span>Chirper</li><li><span></span>Searchly</li><li><span></span>Workwire</li><li><span></span>Viewtube</li>
  </ul>
  <div class="abs contact-col"><svg width="8" height="6" viewBox="0 0 24 18" style="margin-top:3px"><rect x="1" y="1" width="22" height="16" rx="2" fill="var(--green)"/></svg><div>Email:<br>info@tarnlock.com</div></div>

  <div class="abs field mini-field" style="top:1034px">Enter Name</div>
  <div class="abs field mini-field" style="top:1057px">Enter Company</div>
  <div class="abs field mini-field" style="top:1080px">Enter Country</div>
  <div class="abs mini-submit">SUBMIT</div>

  <div class="abs divider"></div>
  <div class="abs copy">© COPYRIGHT 2022 TARN LOCK, ALL RIGHTS RESERVED</div>
  <div class="abs to-top"><svg width="6" height="9" viewBox="0 0 6 9"><path d="M3 9V1M.5 3.5 3 1l2.5 2.5" stroke="#111" fill="none"/></svg></div>
</div>
</body>
</html>
```